Upmarket Dessert Lounge needs a Business Card Design

We are an upmarket dessert lounge needing a business card to match our image.

We want something that is simple yet beautiful, feminine, classy, sophisticated and elegant. We want it to stand out and don't mind if it is bold.

The design should include our logo and colours of red or maroon with gold highlights. We don't mind if black is used.

Marlow & Quince

Target Market(s)

For those who like to indulge or treat themselves and give in to their temptations on good quality desserts.

Industry/Entity Type

Business

Requirements
Must have
• Must include our logo and our name

Marlow & Quince

M & Q

```html
<!DOCTYPE html>
<html lang="en">
<head>
<meta charset="utf-8">
<title>Marlow &amp; Quince — Business Card</title>
<link rel="stylesheet" href="https://fonts.googleapis.com/css2?family=Source+Sans+3:wght@400;600;700&display=swap">
<style>
  :root {
    --maroon: #7a1416;
    --peach: #fdd3a0;
    --peach-deep: #f3c38c;
    --white: #ffffff;
    --stage: #efe7dc;
  }
  * { box-sizing: border-box; margin: 0; padding: 0; }
  html, body { width: 1200px; height: 402px; overflow: hidden; }
  body {
    background: var(--stage);
    font-family: "Source Sans 3", "Helvetica Neue", Arial, sans-serif;
    color: var(--maroon);
    position: relative;
  }
  .card {
    position: absolute;
    top: 54px;
    width: 509px;
    height: 292px;
    background: var(--peach);
    overflow: hidden;
  }
  .card--front { left: 58px; }
  .card--back { left: 632px; }

  .front-shapes { position: absolute; inset: 0; }

  .brand-name {
    position: absolute;
    font-weight: 600;
    color: var(--maroon);
    white-space: nowrap;
    transform: translate(-50%, -50%);
  }
  .card--front .brand-name { left: 148px; top: 150px; font-size: 25px; letter-spacing: 0.5px; }
  .card--back .brand-name { left: 254px; top: 146px; font-size: 72px; letter-spacing: 1px; }

  .contact {
    position: absolute;
    right: 18px;
    top: 24px;
    text-align: right;
    font-size: 12.5px;
    line-height: 15px;
  }
  .contact__name { font-size: 16.5px; font-weight: 700; line-height: 18px; }
  .contact__title { margin-bottom: 22px; }
  .contact__address { margin-bottom: 28px; }
  .contact__row { display: flex; justify-content: flex-end; align-items: center; gap: 5px; height: 18.5px; }
  .contact__row svg { width: 10px; height: 10px; flex: none; }

  .flourish-band {
    position: absolute;
    left: 270px;
    bottom: 8px;
    width: 230px;
    height: 48px;
    border-radius: 24px;
    background: radial-gradient(ellipse at center, var(--peach-deep) 0%, rgba(243,195,140,0) 70%);
  }
</style>
</head>
<body>

<section class="card card--front" aria-label="Business card front">
  <svg class="front-shapes" viewBox="0 0 509 292" width="509" height="292" aria-hidden="true">
    <path fill="var(--maroon)" d="M300 0 H336 C350 125 315 230 205 292 H190 C285 225 322 110 300 0 Z"/>
    <path fill="var(--white)" d="M0 0 H302 C320 110 290 225 192 292 H0 Z"/>
    <path fill="none" stroke="var(--white)" stroke-width="2" d="M336 0 C350 125 315 230 205 292"/>
  </svg>

  <div class="brand-name">Marlow &amp; Quince</div>

  <div class="flourish-band" role="img" aria-label="Faint ornamental flourish"></div>

  <div class="contact">
    <div class="contact__name">Your name</div>
    <div class="contact__title">Title</div>
    <div class="contact__address">
      <div>Street Name</div>
      <div>City Name</div>
      <div>State Zip Code</div>
    </div>
    <div class="contact__row">555-014-2020
      <svg viewBox="0 0 10 10"><circle cx="5" cy="5" r="4.4" fill="none" stroke="var(--maroon)" stroke-width="1"/><path d="M3.4 2.8 L4.3 2.6 L4.7 3.9 L4.1 4.4 Q4.7 5.6 5.7 6.1 L6.2 5.5 L7.4 5.9 L7.2 6.9 Q4.5 7.2 3.4 2.8Z" fill="var(--maroon)"/></svg>
    </div>
    <div class="contact__row">555-014-2020
      <svg viewBox="0 0 10 10"><rect x="2.8" y="0.8" width="4.4" height="8.4" rx="0.8" fill="var(--maroon)"/><rect x="3.6" y="2" width="2.8" height="3.4" fill="var(--peach)"/></svg>
    </div>
    <div class="contact__row">info@marlow&amp;quince.com
      <svg viewBox="0 0 10 10"><rect x="0.8" y="2.2" width="8.4" height="5.8" fill="var(--maroon)"/><path d="M0.8 2.4 L5 5.6 L9.2 2.4" fill="none" stroke="var(--peach)" stroke-width="0.8"/></svg>
    </div>
    <div class="contact__row">www.marlow&amp;quince.com
      <svg viewBox="0 0 10 10"><circle cx="5" cy="5" r="4.3" fill="var(--maroon)"/><path d="M0.8 5 H9.2 M5 0.8 V9.2 M5 0.8 Q2.4 5 5 9.2 M5 0.8 Q7.6 5 5 9.2" fill="none" stroke="var(--peach)" stroke-width="0.6"/></svg>
    </div>
  </div>
</section>

<section class="card card--back" aria-label="Business card back">
  <div class="brand-name">M &amp; Q</div>
</section>

</body>
</html>
```